Website Design for Wheels for Servicemen.org - Donated Cars to Disabled Vets

Need a Wordpress website. The coding now, esp. the CDONT coding is not supported by many hosting sites. Looking for a landing page to generate leads.

Logo Text

look at current one for ideas

Coding

Coded - Design and coding required

Number of Pages Required

1 page

Requirements
Must have
• look at current website at www.wheelsforservicemen.org
Nice to have
• look at this site: http://givevehicletoservicemen.org

```html
<!DOCTYPE html>
<html lang="en">
<head>
<meta charset="utf-8">
<title>Wheels for Servicemen – Donate Your Car</title>
<link href="https://fonts.googleapis.com/css2?family=Lato:wght@400;700&family=Open+Sans:wght@400;600&display=swap" rel="stylesheet">
<style>
:root{
  --red:#d4161e;
  --red-dark:#8e0b10;
  --blue:#0d5cb8;
  --blue-deep:#0a4a9c;
  --blue-band:#0b55ad;
  --navy:#0a3f86;
  --grey-text:#8a8a8a;
  --grey-bg:#f1f1f1;
  --badge:#e4e4e4;
  --line:#d9d9d9;
  --white:#ffffff;
}
*{box-sizing:border-box;margin:0;padding:0}
html,body{width:686px;height:1200px;overflow:hidden;background:var(--white)}
body{position:relative;font-family:'Lato',sans-serif;color:#444}
.abs{position:absolute}

/* header */
.brand{left:87px;top:24px;display:flex;align-items:center;gap:6px;font-size:15px;color:var(--red);font-weight:700}
.brand-dot{width:14px;height:14px;border-radius:50%;background:var(--red)}
.callout{right:88px;top:25px;text-align:right}
.callout-label{font-size:10px;color:var(--red)}
.callout-phone{font-size:15px;color:var(--blue);display:flex;align-items:center;gap:3px;justify-content:flex-end}

/* nav */
.nav{left:0;top:67px;width:686px;height:31px;background:var(--red)}
.nav ul{list-style:none;position:absolute;left:85px;top:0;display:flex;height:31px}
.nav li{color:var(--white);font-size:9px;font-weight:700;display:flex;align-items:center;justify-content:center;border-right:1px solid rgba(0,0,0,.15);height:31px}
.nav li.active{background:var(--red-dark)}

/* hero */
.hero{left:0;top:98px;width:686px;height:258px;background:
  radial-gradient(ellipse 120px 70px at 330px 170px,rgba(255,255,255,.55),rgba(255,255,255,0)),
  linear-gradient(100deg,#9b9b9b 0%,#c4c4c4 45%,#aaaaaa 70%,#bcbcbc 100%)}
.hero-title{left:87px;top:208px;font-weight:700;line-height:1.05}
.hero-title .l1{color:var(--blue);font-size:20px}
.hero-title .l2{color:var(--red);font-size:24px}
.dots{left:90px;top:266px;display:flex;gap:5px}
.dots span{width:7px;height:7px;border-radius:50%;background:#111}
.dots span.on{background:var(--white);border:1.5px solid #111}

/* form */
.donate-form{left:418px;top:122px;width:183px;height:206px;background:var(--blue)}
.donate-form h3{height:30px;background:var(--navy);color:var(--white);font-weight:400;font-size:13px;display:flex;align-items:center;justify-content:center}
.fields{padding:10px 11px 0;display:grid;grid-template-columns:1fr 1fr;gap:4px}
.field{height:19px;background:var(--white);font-size:6.5px;color:#999;padding:6px 7px 0}
.field.wide{grid-column:1/3}
.donate-btn{margin:6px 11px 0;height:22px;background:var(--red);color:var(--white);font-size:9px;display:flex;align-items:center;justify-content:center}

/* steps */
.step{top:336px;width:180px;text-align:center}
.step-ring{margin:0 auto;width:92px;height:92px;border-radius:50%;background:var(--white);border:1px solid #ddd;display:flex;align-items:center;justify-content:center}
.step-ring div{width:76px;height:76px;border-radius:50%;border:2px solid var(--blue);display:flex;align-items:center;justify-content:center}
.step h4{margin-top:11px;font-weight:400;font-size:13px;color:var(--blue)}
.step h4 b{color:var(--red);font-weight:400}
.step p{margin-top:5px;font-family:'Open Sans',sans-serif;font-size:6.6px;line-height:1.65;color:var(--grey-text)}

/* why band */
.why{left:0;top:552px;width:686px;height:243px;background:linear-gradient(120deg,var(--blue-deep),var(--blue-band) 50%,#0a4b9a)}
.notch{left:334px;top:552px;width:0;height:0;border-left:14px solid transparent;border-right:14px solid transparent;border-top:14px solid var(--white)}
.why h2{position:absolute;top:32px;width:100%;text-align:center;color:var(--white);font-size:15px;font-weight:700}
.feat{color:var(--white);display:flex;gap:8px}
.feat h5{font-size:11px;font-weight:700}
.feat p{font-family:'Open Sans',sans-serif;font-size:7.5px;line-height:1.45;margin-top:4px;color:#e3ecf8}
.view-more{left:307px;top:755px;width:87px;height:21px;border:1.5px solid var(--white);color:var(--white);font-size:7.5px;font-weight:700;display:flex;align-items:center;justify-content:center}

/* program */
.program{left:0;top:795px;width:686px;height:219px;background:var(--grey-bg)}
.program h2{position:absolute;top:18px;width:100%;text-align:center;font-weight:400;font-size:16px;color:#444}
.card{top:55px;width:122px;height:130px;background:var(--white);box-shadow:0 1px 2px rgba(0,0,0,.15)}
.card-img{height:68px}
.card h6{padding:8px 10px 0;font-size:8.5px;font-weight:400;color:var(--blue);line-height:1.2}
.card p{padding:3px 10px 0;font-family:'Open Sans',sans-serif;font-size:5.6px;line-height:1.6;color:#aaa}

/* footer */
.foot-col{top:1041px}
.foot-col h4{font-weight:400;font-size:12px;color:var(--blue);margin-bottom:8px}
.foot-col li{list-style:none;font-family:'Open Sans',sans-serif;font-size:7.5px;color:#666;line-height:15px}
.foot-col p{font-family:'Open Sans',sans-serif;font-size:7.5px;color:#666}
.social{display:flex;gap:4px;margin-top:9px}
.social span{width:17px;height:17px;border-radius:50%}
.badge-rect{left:485px;top:1043px;width:76px;height:28px;background:var(--badge);border-radius:3px}
.badge-circle{left:503px;top:1085px;width:30px;height:30px;border-radius:50%;background:var(--badge)}
.rule{left:86px;top:1162px;width:515px;height:1px;background:var(--line)}
.copy{top:1175px;width:686px;text-align:center;font-family:'Open Sans',sans-serif;font-size:7.5px;color:#888}
</style>
</head>
<body>

<header>
  <div class="abs brand"><span class="brand-dot"></span>Wheels for Servicemen</div>
  <div class="abs callout">
    <div class="callout-label">Call Us Today</div>
    <div class="callout-phone">
      <svg width="12" height="12" viewBox="0 0 24 24"><path fill="#d4161e" d="M6.6 10.8a15 15 0 0 0 6.6 6.6l2.2-2.2c.3-.3.7-.4 1-.2 1.1.4 2.3.6 3.6.6.6 0 1 .4 1 1V20c0 .6-.4 1-1 1A17 17 0 0 1 3 4c0-.6.4-1 1-1h3.5c.6 0 1 .4 1 1 0 1.3.2 2.5.6 3.6.1.3 0 .7-.2 1z"/></svg>
      1800-555-0142
    </div>
  </div>
</header>

<nav class="abs nav">
  <ul>
    <li class="active" style="width:83px">HOME</li>
    <li style="width:82px">ABOUT US</li>
    <li style="width:78px">SERVICES</li>
    <li style="width:94px">DONATE CAR</li>
    <li style="width:78px">WHY US</li>
    <li style="width:96px">CONTACT US</li>
  </ul>
</nav>

<section class="abs hero" role="img" aria-label="Greyscale photo of a soldier holding a child, with a white car in front"></section>
<div class="abs hero-title"><div class="l1">DONATE YOUR CAR</div><div class="l2">TO VETERANS</div></div>
<div class="abs dots"><span class="on"></span><span></span><span></span><span></span></div>

<form class="abs donate-form">
  <h3>Want to Donate Now</h3>
  <div class="fields">
    <div class="field wide">Name</div>
    <div class="field wide">Email</div>
    <div class="field">Phone</div><div class="field">Cell phone</div>
    <div class="field">City</div><div class="field">Address</div>
    <div class="field">State</div><div class="field">Zip Code</div>
  </div>
  <div class="donate-btn">DONATE NOW</div>
</form>

<div class="abs step" style="left:72px">
  <div class="step-ring"><div>
    <svg width="34" height="34" viewBox="0 0 24 24" fill="none" stroke="#d4161e" stroke-width="1.6"><path d="M4 4h16v12H11l-4 4v-4H4z"/><path d="M9 7c0 3 2 5 5 5l1-1.5-2-1-1 .8c-.8-.4-1.4-1-1.8-1.8l.8-1-1-2z" fill="#d4161e" stroke="none"/></svg>
  </div></div>
  <h4><b>1.</b> Call Us Now</h4>
  <p>Anterdum vel blandit sed nulla In<br>ullamcorper est eget tempor cursus neque<br>mi consectetuer mi a ultricie</p>
</div>
<div class="abs step" style="left:249px">
  <div class="step-ring"><div>
    <svg width="36" height="30" viewBox="0 0 36 30"><circle cx="6" cy="8" r="3" fill="#d4161e"/><path d="M8 10l8 6" stroke="#d4161e" stroke-width="2"/><path d="M14 14l16-8 2 14-12 2z" fill="#d4161e"/><circle cx="20" cy="20" r="3" fill="#fff" stroke="#d4161e" stroke-width="1.5"/></svg>
  </div></div>
  <h4><b>2.</b> We Tow it</h4>
  <p>Anterdum vel blandit sed nulla In<br>ullamcorper est eget tempor cursus neque<br>mi consectetuer mi a ultricie</p>
</div>
<div class="abs step" style="left:433px">
  <div class="step-ring"><div>
    <svg width="30" height="34" viewBox="0 0 24 28" fill="none" stroke="#d4161e" stroke-width="1.6"><path d="M5 2h14v18l-6 6H5z"/><path d="M9 12l6-6"/><circle cx="9.5" cy="6.5" r="1.2"/><circle cx="14.5" cy="11.5" r="1.2"/><path d="M2 19l3 4 6-7"/></svg>
  </div></div>
  <h4><b>3.</b> Tax Write Off</h4>
  <p>Anterdum vel blandit sed nulla In<br>ullamcorper est eget tempor cursus neque<br>mi consectetuer mi a ultricie</p>
</div>

<section class="abs why" role="img" aria-label="Blue toned photo of American flags">
  <h2>Why Donate Your Car to Us?</h2>
</section>
<div class="abs notch"></div>

<div class="abs feat" style="left:106px;top:625px;width:230px">
  <svg width="22" height="22" viewBox="0 0 24 24" fill="none" stroke="#fff" stroke-width="1.8"><path d="M20 4H3v17h17v-8"/><path d="M7 11l4 4 10-11"/></svg>
  <div><h5>IRS 501(c)3 Approved:</h5><p>Free 24/7 Pickup with No DMV Hassles.</p></div>
</div>
<div class="abs feat" style="left:350px;top:630px;width:250px">
  <svg width="20" height="36" viewBox="0 0 20 36" fill="none" stroke="#fff" stroke-width="2"><path d="M4 2h12l-6 8zM10 10v10"/><path d="M10 20c4 0 5 4 3 7s-7 2-7-2"/></svg>
  <div><h5>Free Local Towing to You</h5><p>We will pick up your car donation, running or not,<br>when it's most convenient, at home or work</p></div>
</div>
<div class="abs feat" style="left:98px;top:692px;width:240px">
  <svg width="32" height="24" viewBox="0 0 32 24" fill="#fff"><path d="M5 10l3-7h16l3 7h3v8h-3v4h-4v-4H9v4H5v-4H2v-8z"/><rect x="9" y="5" width="14" height="5" fill="#0b55ad"/><circle cx="8" cy="14" r="2" fill="#0b55ad"/><circle cx="24" cy="14" r="2" fill="#0b55ad"/></svg>
  <div><h5>All Cars Accepted</h5><p>We take your car regardless of its condition or<br>registration status.</p></div>
</div>
<div class="abs feat" style="left:348px;top:692px;width:265px">
  <svg width="30" height="30" viewBox="0 0 30 30" fill="#fff"><path d="M13 0h4v8h4l-6 6-6-6h4z"/><ellipse cx="8" cy="20" rx="5" ry="2"/><ellipse cx="8" cy="25" rx="5" ry="2"/><ellipse cx="20" cy="17" rx="5" ry="2"/><ellipse cx="20" cy="22" rx="5" ry="2"/><ellipse cx="20" cy="27" rx="5" ry="2"/></svg>
  <div><h5>Income Tax Deduction</h5><p>We issue you an IRS tax receipt &amp; offer the largest resale<br>network to get you the highest tax write-off possible.</p></div>
</div>
<div class="abs view-more">VIEW MORE</div>

<section class="abs program">
  <h2>Car Donation Program</h2>
  <div class="abs card" style="left:86px">
    <div class="card-img" role="img" aria-label="Dark teal world map graphic" style="background:linear-gradient(135deg,#12303a,#1d5563)"></div>
    <h6>Donation Accepted<br>Nationalwide</h6>
    <p>Curabitur iaculis tempus eros Cura<br>bitur vel mi sit amet magna</p>
  </div>
  <div class="abs card" style="left:216px">
    <div class="card-img" role="img" aria-label="Black SUV on an autumn road" style="background:linear-gradient(180deg,#c48a3a,#3a3a3a 70%,#8c7a5a)"></div>
    <h6>All Vehicles Type<br>Welcome</h6>
    <p>Curabitur iaculis tempus eros Cura<br>bitur vel mi sit amet magna</p>
  </div>
  <div class="abs card" style="left:346px">
    <div class="card-img" role="img" aria-label="Hand with pen over paperwork and a calculator" style="background:linear-gradient(135deg,#cfcfcf,#f0f0f0 60%,#b8a48c)"></div>
    <h6>We take care of all<br>Paperwork.</h6>
    <p>Curabitur iaculis tempus eros Cura<br>bitur vel mi sit amet magna</p>
  </div>
  <div class="abs card" style="left:476px">
    <div class="card-img" role="img" aria-label="Soldier with a child holding a small flag in a park" style="background:linear-gradient(135deg,#5c7a3a,#8fb35a 60%,#3f5c2a)"></div>
    <h6>And we take care of<br>DMV &amp; Smog issues.</h6>
    <p>Curabitur iaculis tempus eros Cura<br>bitur vel mi sit amet magna</p>
  </div>
</section>

<footer>
  <div class="abs foot-col" style="left:92px">
    <h4>Quick Links</h4>
    <ul><li>About Us</li><li>What We Do</li><li>How it works</li><li>Members</li></ul>
  </div>
  <div class="abs foot-col" style="left:214px">
    <h4>Resources</h4>
    <ul><li>Support</li><li>FAQ</li><li>Term of Use</li><li>Contact Us</li></ul>
  </div>
  <div class="abs foot-col" style="left:330px">
    <h4>Connect With Us</h4>
    <p>Please connect with us on these</p>
    <div class="social"><span style="background:#3aa4dc"></span><span style="background:#2a4f8f"></span><span style="background:#1a6e96"></span><span style="background:#d44a36"></span></div>
  </div>
  <div class="abs badge-rect" role="img" aria-label="Security partner badge"></div>
  <div class="abs badge-circle" role="img" aria-label="Approved charity seal"></div>
  <div class="abs rule"></div>
  <div class="abs copy">© 2016 Company Name &nbsp;All right reserved</div>
</footer>

</body>
</html>
```